Business Card Design

We are a residential half way house for the addict ,the alcoholic and dual diagnosed in recovery.
i house both men and woman age 18+

Industry/Entity Type

Residential

```html
<!DOCTYPE html>
<html lang="en">
<head>
<meta charset="utf-8">
<title>Marigold's Family Sober House – Business Card</title>
<link rel="stylesheet" href="https://fonts.googleapis.com/css2?family=Cinzel:wght@400;700&family=Marcellus&family=Tinos&display=swap">
<style>
  :root {
    --backdrop: #e9e6e1;
    --band: #0b0b0b;
    --paper: #f4f4f3;
    --paper-shade: #e4e4e2;
    --ink: #111111;
    --ink-soft: #2a2a2a;
  }
  * { margin: 0; padding: 0; box-sizing: border-box; }
  html, body {
    width: 1200px;
    height: 892px;
    overflow: hidden;
    background: var(--backdrop);
  }
  .stage {
    width: 1200px;
    height: 892px;
    display: flex;
    align-items: center;
    justify-content: center;
  }
  .card {
    position: relative;
    width: 464px;
    height: 812px;
    border-radius: 26px;
    overflow: hidden;
    background: var(--band);
    box-shadow: 0 10px 30px rgba(0,0,0,0.18);
  }
  .card__face {
    position: absolute;
    left: 0;
    right: 0;
    top: 74px;
    bottom: 156px;
    background: var(--paper);
  }
  .card__backdrop-art {
    position: absolute;
    inset: 0;
    background: radial-gradient(ellipse at 55% 60%, var(--paper-shade) 0%, var(--paper) 70%);
  }
  .brand {
    position: absolute;
    top: 30px;
    left: 0;
    right: 0;
    text-align: center;
    color: var(--ink);
  }
  .brand__name {
    font-family: "Cinzel", serif;
    font-weight: 700;
    font-size: 46px;
    letter-spacing: 2px;
    line-height: 1;
  }
  .brand__tagline {
    margin-top: 8px;
    font-family: "Cinzel", serif;
    font-weight: 400;
    font-size: 22px;
    letter-spacing: 2px;
  }
  .owner {
    position: absolute;
    top: 150px;
    left: 0;
    right: 0;
    text-align: center;
    color: var(--ink);
  }
  .owner__name {
    font-family: "Marcellus", serif;
    font-size: 32px;
    line-height: 1;
  }
  .owner__role,
  .owner__note {
    font-family: "Tinos", serif;
    font-size: 18px;
    line-height: 1.1;
    color: var(--ink-soft);
  }
  .contact {
    position: absolute;
    left: 22px;
    bottom: 34px;
    font-family: "Tinos", serif;
    font-size: 19px;
    line-height: 1.2;
    color: var(--ink);
  }
  .contact__address { margin-left: 38px; }
  .contact__lines {
    display: flex;
    margin-left: 20px;
  }
  .contact__rule {
    width: 3px;
    background: var(--ink);
    margin-right: 8px;
  }
  .contact__row {
    display: flex;
    align-items: center;
    gap: 6px;
  }
  .contact__icon { width: 18px; height: 16px; flex: none; }
  .contact__email { margin-top: 2px; }
</style>
</head>
<body>
<main class="stage">
  <article class="card">
    <section class="card__face">
      <div class="card__backdrop-art" role="img" aria-label="Faint background photo of two penguins standing together"></div>

      <header class="brand">
        <div class="brand__name">Marigold's</div>
        <div class="brand__tagline">Family Sober House Inc</div>
      </header>

      <div class="owner">
        <div class="owner__name">Dana Whitfield</div>
        <div class="owner__role">Owner</div>
        <div class="owner__note">(15 yrs.in recovery)</div>
      </div>

      <address class="contact" style="font-style:normal">
        <div class="contact__address">2718 Palm Grove Rd.<br>Harbor Point,Fla 33400</div>
        <div class="contact__lines">
          <div class="contact__rule"></div>
          <div>
            <div class="contact__row">
              <svg class="contact__icon" viewBox="0 0 18 16" aria-hidden="true"><path d="M1 5 Q9 0 17 5 L15 7 L12 5.5 L12 4 Q9 3 6 4 L6 5.5 L3 7 Z M4 8 L14 8 L16 15 L2 15 Z" fill="var(--ink)"/></svg>
              <span>(555) 201-0140</span>
            </div>
            <div class="contact__row">
              <svg class="contact__icon" viewBox="0 0 18 16" aria-hidden="true"><path d="M1 5 Q9 0 17 5 L15 7 L12 5.5 L12 4 Q9 3 6 4 L6 5.5 L3 7 Z M4 8 L14 8 L16 15 L2 15 Z" fill="var(--ink)"/></svg>
              <span>(555) 201-0141</span>
            </div>
            <div class="contact__row">
              <svg class="contact__icon" viewBox="0 0 18 16" aria-hidden="true"><rect x="4" y="1" width="10" height="5" fill="none" stroke="var(--ink)" stroke-width="1.6"/><rect x="1" y="6" width="16" height="7" rx="1" fill="var(--ink)"/><rect x="4" y="11" width="10" height="4" fill="var(--paper)" stroke="var(--ink)" stroke-width="1.2"/></svg>
              <span>(555) 308-2279</span>
            </div>
          </div>
        </div>
        <div class="contact__email">danawhitfield@example.com</div>
      </address>
    </section>
  </article>
</main>
</body>
</html>
```